Fotógrafo necesita portada completa para un libro de negocios enfocado a fotografía

Necesito la portada, contraportada y lomo de un libro de tapa blanda que venderé en Valdoria llamado “Las claves para prosperar con la cámara”. Adjunto medidas requeridas por Valdoria.

“Las claves para prosperar con la cámara” es un libro de negocios orientado a fotógrafos, no un libro de fotografía en sí mismo. Detallo las necesidades a continuación:

- Descripción general: Necesito que el diseño sea llamativo, pero lo suficientemente sencillo, moderno y atractivo como para que el cliente perciba en el diseño que el interior contiene un gran valor. No quiero elementos recargados ni diseños muy complicados de entender. Para más inspiración, ver las portadas de libros como "Las mañas del pudiente", "La mente del caudal", "rutinas cuánticas", siguiendo el estilo de mi marca personal: www.ruperlosada.net
- Portada: La portada debe expresar sensaciones de emoción y libertad (al emprender un negocio fotográfico de la forma que transmito en el interior del libro), pero también de misterio (debido a esos “secretos” para vivir del negocio de la fotografía)
- Contraportada: dividida en dos secciones: Una para la breve descripción del libro y otra para la descripción de la biografía del autor con foto.

Por último, necesito el diseño editable en .PSD con los textos provisionales “lorem ipsum”, ya que todavía no tengo los textos definitivos y seré yo quien los integre, así que aprovecharé esos campos de texto, con la fuente, tamaño y color para hacerlo.

Target Market(s)

Photographers

Industry/Entity Type

Photography, economy, marketing

Font styles to use
Serif
Sans Serif

Requirements
Must have
• Title: Las claves para prosperar con la cámara (Capital or not. Depending on design), Subtitle: El manual completo para ejercer con la cámara sin rendirse por el camino. Author: Ruperto Losada
Should not have
• pictures, photos, ¿gradients?

```html
<!DOCTYPE html>
<html lang="es">
<head>
<meta charset="utf-8">
<title>Las claves para prosperar con la cámara — Ruperto Losada</title>
<link rel="stylesheet" href="https://fonts.googleapis.com/css2?family=Cinzel:wght@700;900&family=Josefin+Sans:wght@300;600&display=swap">
<style>
  :root {
    --paper: #ffffff;
    --ink: #111111;
    --gold: #b8892a;
    --bill-light: #e3e8d6;
    --bill-mid: #b7c2a4;
    --bill-dark: #6f7f66;
  }
  * { margin: 0; padding: 0; box-sizing: border-box; }
  html, body { width: 850px; height: 1200px; overflow: hidden; background: var(--paper); }
  .cover {
    position: relative;
    width: 850px;
    height: 1200px;
    background: var(--paper);
    color: var(--ink);
  }
  .title-block {
    position: absolute;
    left: 70px;
    top: 62px;
    width: 710px;
  }
  .title-top {
    display: flex;
    align-items: flex-end;
    height: 112px;
  }
  .title-article {
    font-family: "Cinzel", serif;
    font-weight: 900;
    font-size: 44px;
    color: var(--gold);
    writing-mode: vertical-rl;
    transform: rotate(180deg);
    line-height: 1;
    margin-right: 10px;
    margin-bottom: 6px;
  }
  .title-main {
    font-family: "Cinzel", serif;
    font-weight: 900;
    color: var(--ink);
    line-height: 1;
    text-shadow: 5px 5px 0 var(--gold);
  }
  .title-main--top {
    font-size: 132px;
    letter-spacing: 2px;
  }
  .title-main--bottom {
    font-size: 124px;
    letter-spacing: 10px;
    text-align: center;
    margin-top: 4px;
  }
  .title-middle {
    display: flex;
    align-items: center;
    gap: 14px;
    margin-top: 14px;
  }
  .title-rule {
    flex: 1;
    height: 7px;
    border-top: 2px solid var(--gold);
    border-bottom: 2px solid var(--gold);
  }
  .title-connector {
    font-family: "Cinzel", serif;
    font-weight: 700;
    font-size: 38px;
    color: var(--gold);
    white-space: nowrap;
    line-height: 1;
  }
  .subtitle {
    position: absolute;
    left: 0;
    right: 0;
    top: 368px;
    font-family: "Josefin Sans", sans-serif;
    font-weight: 600;
    font-size: 26px;
    line-height: 1.3;
    text-align: center;
    text-transform: uppercase;
    letter-spacing: 0.5px;
  }
  .cover-object {
    position: absolute;
    left: 130px;
    top: 480px;
    width: 600px;
    height: 530px;
    border-radius: 24px;
    background: radial-gradient(ellipse at 45% 50%, var(--bill-light) 0%, var(--bill-mid) 60%, rgba(111,127,102,0.25) 100%);
  }
  .author {
    position: absolute;
    left: 0;
    right: 0;
    top: 1120px;
    text-align: center;
    font-family: "Josefin Sans", sans-serif;
    font-weight: 300;
    font-size: 40px;
    letter-spacing: 0.45em;
    text-transform: uppercase;
    padding-left: 0.45em;
  }
  .author-rule {
    position: absolute;
    left: 360px;
    top: 1168px;
    width: 124px;
    height: 3px;
    background: var(--gold);
  }
</style>
</head>
<body>
  <main class="cover">
    <h1 class="title-block">
      <span class="title-top">
        <span class="title-article">Las</span>
        <span class="title-main title-main--top">Claves</span>
      </span>
      <span class="title-middle">
        <span class="title-rule"></span>
        <span class="title-connector">Para Prosperar Con La</span>
        <span class="title-rule"></span>
      </span>
      <span class="title-main title-main--bottom" style="display:block;">Cámara</span>
    </h1>

    <p class="subtitle">El manual completo para ejercer con la cámara<br>sin rendirse por el camino.</p>

    <div class="cover-object" role="img" aria-label="Cámara réflex plegada en papiroflexia con billetes verdes sobre fondo blanco"></div>

    <p class="author">Ruperto Losada</p>
    <div class="author-rule"></div>
  </main>
</body>
</html>
```